Banner to be displayed at local Farmers Market Booth.

Graphic Design Brief: Farmers Market Banner Contest

Project Overview:We are seeking talented graphic designers to create a visually appealing banner for our booth at the local farmers market. Our company specializes in healthy, all-natural dog and cat treats, and we want a banner that captures our brand identity while drawing in pet owners who value quality and nutrition for their furry friends.

Banner Specifications:

Size: 24 inches x 60 inches (Horizontal orientation) 24" High X 60 wide

Theme: Vintage/Retro

Style: Warm, inviting, nostalgic with a touch of rustic charm

Colors: Earthy, muted tones such as warm browns, soft greens, and creamy yellows. Pops of red or blue may be used sparingly for accents. OR Black and White with gray scales. Would like to see both

Typography: Retro-style fonts that are readable and align with the vintage aesthetic.

Key Elements to Include: website (www.moltbyfarms.com)

Company Name: Moltby Farms

Tagline: " Simply Honest Bites "
Imagery: Illustrations or stylized graphics of happy dogs and cats, possibly interacting with treats.

Emphasis on Natural Ingredients: Icons or design elements that subtly suggest freshness and quality (e.g., leaves, wheat, bones, or paw prints).

Farmers Market Appeal: A design that blends well with the artisanal, handmade, and farm-fresh atmosphere of the market.

Design Considerations:

The banner should be easily readable from a distance.

A balanced composition that doesn't feel overcrowded.

Should evoke trust and warmth while maintaining a professional look.

Avoid overly modern or sleek elements that don’t align with the vintage aesthetic.

Submission Requirements:

High-resolution digital file in PDF or AI format.

CMYK color mode for printing purposes.

Must include a mockup or preview of how it would look in a real farmers market setting.

We look forward to seeing your creative interpretations of our brand! If you have any questions, feel free to reach out.

Font styles to use
Other font styles liked:
• See attachement

Requirements
Nice to have
• Retro/Vintage,playful BUT NOT whimsical

```html
<!DOCTYPE html>
<html lang="en">
<head>
<meta charset="UTF-8">
<title>Moltby Farms – Market Banner</title>
<link href="https://fonts.googleapis.com/css2?family=Anton&family=Bowlby+One&family=Sniglet:wght@800&display=swap" rel="stylesheet">
<style>
  :root {
    --page-bg: #ebebeb;
    --frame-brown: #4a3422;
    --frame-stripe: #5f4a2c;
    --panel-cream: #f1e5c9;
    --panel-line: #6b3a22;
    --title-brown: #5b2414;
    --title-shadow: #e0a25a;
    --olive: #4b4f2a;
    --olive-shadow: #e3b26a;
    --pill-red: #9a3016;
    --pill-text: #fff8ec;
    --sun-yellow: #f0bd3a;
    --coat-gold: #c48a45;
  }
  * { margin: 0; padding: 0; box-sizing: border-box; }
  html, body { width: 964px; height: 1200px; overflow: hidden; background: var(--page-bg); }

  .banner {
    position: absolute;
    left: 32px; top: 420px;
    width: 900px; height: 360px;
    background:
      repeating-linear-gradient(90deg, var(--frame-brown) 0 3px, var(--frame-stripe) 3px 6px);
    box-shadow: 0 10px 24px rgba(0,0,0,.22);
    overflow: hidden;
  }
  .banner__panel { position: absolute; left: 0; top: 0; }

  .brand-name {
    position: absolute;
    left: 283px; top: 48px;
    transform: translateX(-50%);
    display: flex; align-items: center; gap: 8px;
    font-family: "Sniglet", sans-serif;
    font-weight: 800;
    font-size: 30px;
    color: var(--title-brown);
    white-space: nowrap;
  }
  .brand-name__dot {
    width: 14px; height: 14px; border-radius: 50%;
    background: var(--title-brown);
  }

  .tagline {
    position: absolute;
    left: 59px; width: 460px;
    text-align: center;
    line-height: 1;
  }
  .tagline__top {
    top: 100px;
    font-family: "Anton", sans-serif;
    font-size: 82px;
    letter-spacing: -1px;
    color: var(--title-brown);
    text-shadow: 3px 3px 0 var(--title-shadow);
  }
  .tagline__bottom {
    top: 198px;
    font-family: "Bowlby One", sans-serif;
    font-size: 66px;
    color: var(--olive);
    text-shadow: 4px 3px 0 var(--olive-shadow);
  }

  .web-pill {
    position: absolute;
    left: 69px; top: 288px;
    width: 460px; height: 54px;
    border-radius: 14px;
    background: var(--pill-red);
    display: flex; align-items: center; justify-content: center;
    font-family: "Sniglet", sans-serif;
    font-weight: 800;
    font-size: 36px;
    color: var(--pill-text);
  }

  .pet-photo {
    position: absolute;
    left: 519px; top: 30px;
    width: 381px; height: 330px;
    border-radius: 130px 130px 0 0;
    background: radial-gradient(circle at 52% 40%, var(--coat-gold) 0 38%, var(--sun-yellow) 60%, #d9a84a 100%);
  }
</style>
</head>
<body>
  <section class="banner">
    <svg class="banner__panel" width="900" height="360" viewBox="0 0 900 360" aria-hidden="true">
      <path d="M48 16 H852 A30 30 0 0 0 882 46 V314 A30 30 0 0 0 852 344 H48 A30 30 0 0 0 18 314 V46 A30 30 0 0 0 48 16 Z"
            fill="var(--panel-cream)" stroke="#ffffff" stroke-width="5"/>
      <path d="M52 21 H848 A30 30 0 0 0 877 50 V310 A30 30 0 0 0 848 339 H52 A30 30 0 0 0 23 310 V50 A30 30 0 0 0 52 21 Z"
            fill="none" stroke="var(--panel-line)" stroke-width="1.5"/>
    </svg>

    <div class="brand-name"><span class="brand-name__dot"></span>Moltby Farms</div>

    <h1>
      <span class="tagline tagline__top" style="position:absolute">SIMPLY HONEST</span>
      <span class="tagline tagline__bottom" style="position:absolute">BITES</span>
    </h1>

    <div class="web-pill">moltbyfarms.com</div>

    <div class="pet-photo" role="img" aria-label="Golden retriever and calico cat together behind a bowl of treats, set against a yellow sun circle"></div>
  </section>
</body>
</html>
```